Business Card Design Project - del varosi group

dear Sirs

we need business card design for our group ( DEL Varosi Group ) , i have got the Logo design of our group from pixel harbor in previous , so all need details relating to our group i think available with you, as well as the the chosen logo design

we hope to provide us with business card logo that to be appropaite and satisfactory to us .

thanks

note : logo design of our group is attached .
Updates

Reason: please extend the deadline of my project for additional 15 days because i didn't received appropriate design for our gruop yet . kindly beaware that i have received 77 design till now , supossed to send me 200-250 design at least . thanks

Target Market(s)

contents

name : Kerem EL Nadiri

position : Operation Manager

Industry/Entity Type

Business

Requirements
Must have

• person name

group logo
Nice to have
• logo color matching with back background

```html
<!DOCTYPE html>
<html lang="en">
<head>
<meta charset="utf-8">
<title>DEL Varosi Group – Business Card</title>
<link rel="stylesheet" href="https://fonts.googleapis.com/css2?family=Open+Sans:wght@400;600;700&display=swap">
<style>
  :root {
    --brand-blue: #0f4f94;
    --brand-gold: #d2b26b;
    --text-grey: #5a5a5a;
    --card-white: #ffffff;
    --backdrop: #e9e7e4;
  }
  html, body {
    margin: 0;
    padding: 0;
    width: 1200px;
    height: 758px;
    overflow: hidden;
    background: var(--backdrop);
    font-family: "Open Sans", Arial, sans-serif;
  }
  .canvas {
    position: relative;
    width: 1200px;
    height: 758px;
  }
  .card {
    position: absolute;
    top: 214px;
    width: 530px;
    height: 320px;
    background: var(--card-white);
    border-radius: 22px;
    overflow: hidden;
    box-shadow: 0 10px 26px rgba(0,0,0,0.18);
  }
  .card--front { left: 50px; }
  .card--back  { left: 620px; }

  .brand {
    display: flex;
    align-items: center;
    gap: 12px;
    color: var(--brand-blue);
    font-weight: 600;
    white-space: nowrap;
  }
  .brand__square {
    background: var(--brand-blue);
    flex: none;
  }
  .card--front .brand {
    position: absolute;
    left: 40px;
    top: 40px;
    font-size: 31px;
  }
  .card--front .brand__square { width: 22px; height: 22px; }

  .address {
    position: absolute;
    left: 40px;
    top: 138px;
    margin: 0;
    font-size: 14px;
    color: var(--text-grey);
    letter-spacing: 0.2px;
  }
  .contacts {
    position: absolute;
    left: 40px;
    top: 168px;
    margin: 0;
    padding: 0;
    list-style: none;
    font-size: 13px;
    line-height: 18px;
    color: var(--text-grey);
  }
  .contacts li {
    display: flex;
    align-items: center;
    gap: 6px;
  }
  .contacts svg { width: 10px; height: 10px; fill: var(--text-grey); }

  .person {
    position: absolute;
    right: 40px;
    top: 128px;
    text-align: right;
  }
  .person__name {
    margin: 0;
    font-size: 17px;
    font-weight: 700;
    color: var(--brand-blue);
  }
  .person__role {
    margin: 2px 0 0;
    font-size: 12.5px;
    color: var(--text-grey);
  }

  .wave {
    position: absolute;
    left: 0;
    bottom: 0;
    width: 530px;
    height: 130px;
  }
  .wave__band { fill: var(--brand-blue); }
  .wave__accent { fill: var(--brand-gold); }

  .card--front .website {
    position: absolute;
    right: 36px;
    bottom: 30px;
    font-size: 14px;
    color: var(--card-white);
    letter-spacing: 0.6px;
  }

  .card--back .brand {
    position: absolute;
    left: 0;
    right: 0;
    top: 112px;
    justify-content: center;
    font-size: 38px;
  }
  .card--back .brand__square { width: 26px; height: 26px; }
  .card--back .website {
    position: absolute;
    left: 0;
    right: 0;
    top: 210px;
    text-align: center;
    font-size: 19px;
    color: var(--brand-blue);
    letter-spacing: 1px;
  }
</style>
</head>
<body>
<main class="canvas">

  <section class="card card--front" aria-label="Business card front">
    <div class="brand"><span class="brand__square"></span>DEL Varosi Group</div>

    <p class="address">Street name, City, State, zip code</p>
    <ul class="contacts">
      <li><svg viewBox="0 0 10 10"><rect x="2.5" y="0" width="5" height="10" rx="1"/></svg>+2347031184526</li>
      <li><svg viewBox="0 0 10 10"><path d="M2 0 L4 2.5 L3 4 Q4.5 6 6 7 L7.5 6 L10 8 L8.5 10 Q3 9 0 1.5 Z"/></svg>+2347031184526</li>
      <li><svg viewBox="0 0 10 10"><rect x="0" y="3" width="10" height="6" rx="1"/><rect x="2" y="0" width="6" height="3"/></svg>+2347031184526</li>
      <li><svg viewBox="0 0 10 10"><rect x="0" y="2" width="10" height="7" rx="1"/></svg>name@harborlinehotels.com</li>
    </ul>

    <div class="person">
      <p class="person__name">Kerem EL Nadiri</p>
      <p class="person__role">Operation Manager</p>
    </div>

    <svg class="wave" viewBox="0 0 530 130" preserveAspectRatio="none" aria-hidden="true">
      <path class="wave__band" d="M0 112 C140 122 330 80 530 40 L530 130 L0 130 Z"/>
      <path class="wave__accent" d="M0 84 C150 112 340 62 530 8 L530 20 C330 74 150 120 0 112 Z"/>
    </svg>
    <span class="website">www.website.com</span>
  </section>

  <section class="card card--back" aria-label="Business card back">
    <div class="brand"><span class="brand__square"></span>DEL Varosi Group</div>
    <span class="website">www.website.com</span>
  </section>

</main>
</body>
</html>
```